Willow Fen Racquet Club (Tennis Country Club)

Racquet and Tennis Country Club in Florida.
This web sight is needed for a Privet Tennis club located in Deerfield Beach city in Florida, USA.
We have 10 clay tennis courts and 2 hard tennis courts, small and cozy swimming pool and a clubhouse (see attached pictures) Attached pictures are for information only because we are under a reconstruction.
Updates

I haven't received any source files and web converted files neither!

Target Market(s)

Adult members, Kids members, Tennis players

Coding

Coded - Design and coding required

Number of Pages Required

3 page

Requirements
Must have
• Logo colors (see attached file)

```html
<!DOCTYPE html>
<html lang="en">
<head>
<meta charset="utf-8">
<title>Willow Fen Racquet Club</title>
<link href="https://fonts.googleapis.com/css2?family=Open+Sans:ital,wght@0,400;0,600;0,700;0,800;1,400;1,600&display=swap" rel="stylesheet">
<style>
:root{
  --green:#0e6b35;
  --green-dark:#0a5229;
  --ink:#2f2f2f;
  --charcoal:#444444;
  --text:#5a5a5a;
  --paper:#ffffff;
  --mist:#efefef;
  --footer:#2b2b2b;
}
*{box-sizing:border-box;margin:0;padding:0}
html,body{width:1200px;height:3429px;overflow:hidden}
body{position:relative;background:var(--mist);font-family:"Open Sans",Arial,sans-serif;color:var(--ink)}
.abs{position:absolute}

/* hero */
.hero{left:0;top:0;width:1200px;height:617px;background:radial-gradient(ellipse at 62% 35%,#6b6a4a 0%,#3a3a2c 22%,#151515 55%,#0a0a0a 100%)}
.brand-corner{left:0;top:0}
.brand{left:24px;top:30px;display:flex;align-items:center;gap:10px;font-weight:700;font-size:26px;color:var(--ink)}
.brand .dot{width:30px;height:30px;border:3px solid var(--green);border-radius:50%}
.nav{top:45px;left:0;width:1200px;height:24px}
.nav a{position:absolute;color:#fff;font-weight:700;font-size:16px;text-decoration:none;letter-spacing:.3px}
.hero h1{left:96px;top:258px;font-size:64px;font-weight:800;color:#fff;letter-spacing:1px}
.hero p{left:98px;top:362px;width:620px;font-size:15.5px;line-height:29px;color:#fff}
.btn-outline{left:98px;top:448px;width:119px;height:50px;border:2px solid #fff;color:#fff;font-size:15.5px;display:flex;align-items:center;justify-content:center}
.hero-corner{left:1067px;top:514px}

/* section heads */
.eyebrow{width:1200px;left:0;text-align:center;font-size:16px;color:var(--ink);letter-spacing:.3px}
.section-title{width:1200px;left:0;text-align:center;font-size:40px;font-weight:800;color:var(--ink);letter-spacing:.5px}
.section-title em{font-style:normal;color:var(--green)}
.rule{width:90px;height:3px;left:555px;background:var(--green)}

/* principles */
.principles{left:0;top:617px;width:1200px;height:656px;background:var(--paper)}
.principle{width:230px;text-align:center}
.principle h3{font-size:17px;font-weight:700;margin-top:8px}
.principle p{font-size:13.5px;line-height:19px;color:var(--text);margin-top:8px}
.principle.is-active h3,.principle.is-active p{color:#fff}
.cap-label{width:230px;text-align:center;color:#fff;font-size:15px;font-weight:700}

/* testimonials */
.testimonials{left:0;top:1273px;width:1200px;height:665px;background:linear-gradient(180deg,#1e1d18 0%,#2a2518 45%,#141414 100%)}
.testimonials .eyebrow,.testimonials .section-title{color:#fff}
.testimonials .rule{background:#fff}
.avatar{left:538px;top:1508px;width:124px;height:124px;border-radius:50%;border:4px solid #fff;background:linear-gradient(160deg,#c9a98f,#8a7a6c)}
.quote-badge{left:612px;top:1588px;width:44px;height:44px;border-radius:50%;background:var(--green);border:3px solid #fff;color:#fff;font-weight:800;font-style:italic;font-size:20px;display:flex;align-items:center;justify-content:center}
.person{left:0;width:1200px;top:1654px;text-align:center;color:#fff;font-size:17px;font-weight:700}
.quote{left:98px;width:1004px;top:1694px;text-align:center;color:#fff;font-size:15.5px;line-height:31px;font-style:italic;font-weight:600}

/* programmes */
.programmes{left:98px;top:1826px;width:1004px;height:407px;background:var(--paper);box-shadow:0 2px 10px rgba(0,0,0,.25)}
.programme{width:231px;text-align:center}
.programme .photo{width:231px;height:187px}
.programme .badge{position:absolute;left:84px;top:150px;width:64px;height:64px;border-radius:50%;border:4px solid #fff;display:flex;align-items:center;justify-content:center}
.programme h3{margin-top:50px;font-size:17px;font-weight:700}
.programme p{margin-top:12px;font-size:13.5px;line-height:23px;color:var(--text);padding:0 4px}
.programme.is-green h3{color:var(--green)}

/* gallery */
.gallery{left:98px;top:2457px;width:1004px;height:554px;background:var(--paper)}
.tile{display:flex;align-items:flex-end;justify-content:center;padding-bottom:16px;color:#fff;font-weight:800;font-size:18px;letter-spacing:.2px;text-shadow:0 1px 3px rgba(0,0,0,.5)}

/* footer */
.footer{left:0;top:3097px;width:1200px;height:332px;background:var(--footer)}
.footer-brand{left:1035px;top:3165px;display:flex;align-items:center;gap:8px;font-weight:700;font-size:22px;color:var(--ink)}
.footer-brand .dot{width:26px;height:26px;border:3px solid var(--green);border-radius:50%}
.contact{top:3180px;display:flex;align-items:center;gap:12px;color:#fff;font-weight:700;font-size:16px}
.contact .ring{width:42px;height:42px;border:2px solid #fff;border-radius:50%;display:flex;align-items:center;justify-content:center}
.footer-nav{left:98px;top:3267px;display:flex;gap:0;color:#fff;font-weight:700;font-size:15.5px}
.footer-nav span{padding:0 24px}
.footer-nav span:first-child{padding-left:0}
.footer-nav .sep{padding:0}
.footer-line{left:98px;top:3325px;width:748px;height:2px;background:#bdbdbd}
.copyright{left:98px;top:3365px;color:#fff;font-size:14.5px}
</style>
</head>
<body>

<!-- Hero -->
<section class="abs hero" role="img" aria-label="Tennis player in a yellow shirt hitting a forehand on a night-lit court"></section>
<svg class="abs brand-corner" width="343" height="263" viewBox="0 0 343 263"><polygon points="0,0 343,0 0,263" fill="#fff"/><line x1="343" y1="0" x2="0" y2="263" stroke="var(--green)" stroke-width="3"/></svg>
<div class="abs brand"><span class="dot"></span>Willow Fen</div>
<nav class="abs nav">
  <a style="left:495px">HOME</a>
  <a style="left:603px">ABOUT</a>
  <a style="left:720px">MEMBERSHIP</a>
  <a style="left:884px">SCHEDULE</a>
  <a style="left:1026px">CONTACT</a>
</nav>
<h1 class="abs" style="left:96px;top:258px;font-size:64px;font-weight:800;color:#fff;letter-spacing:1px">WILLOW FEN</h1>
<p class="abs" style="left:98px;top:358px;width:620px;font-size:15.5px;line-height:29px;color:#fff">Nemo enim ipsam voluptatem quia voluptas sit aspernatur aut odit aut fugit, sed quia consequuntur magni dolores.</p>
<div class="abs btn-outline">Read More</div>
<svg class="abs hero-corner" width="133" height="103" viewBox="0 0 133 103">
  <polygon points="0,103 133,0 133,103" fill="#fff"/>
  <polyline points="82,62 72,73 82,84" fill="none" stroke="var(--green)" stroke-width="3"/>
  <polyline points="97,62 107,73 97,84" fill="none" stroke="var(--green)" stroke-width="3"/>
</svg>

<!-- Principles -->
<section class="abs principles"></section>
<div class="abs eyebrow" style="top:682px">TENNIS CLUB</div>
<h2 class="abs section-title" style="top:706px">OUR <em>PRINCIPLES</em></h2>
<div class="abs rule" style="top:781px"></div>

<svg class="abs" style="left:0;top:780px" width="1200" height="400" viewBox="0 0 1200 400">
  <!-- dotted orbits -->
  <path d="M85 226 A171 171 0 0 1 404 131" fill="none" stroke="#2b2b2b" stroke-width="3" stroke-dasharray="1 6" stroke-linecap="round"/>
  <path d="M1115 226 A171 171 0 0 0 796 131" fill="none" stroke="#2b2b2b" stroke-width="3" stroke-dasharray="1 6" stroke-linecap="round"/>
  <circle cx="601" cy="217" r="171" fill="none" stroke="var(--green-dark)" stroke-width="3" stroke-dasharray="1 6" stroke-linecap="round"/>
  <circle cx="85" cy="226" r="6" fill="#fff" stroke="var(--green)" stroke-width="3"/>
  <circle cx="1113" cy="226" r="6" fill="#fff" stroke="var(--green)" stroke-width="3"/>
  <!-- left -->
  <circle cx="256" cy="217" r="137" fill="#fff" stroke="var(--charcoal)" stroke-width="4"/>
  <path d="M143.4 295 A137 137 0 0 0 368.6 295 Z" fill="var(--charcoal)"/>
  <!-- centre -->
  <circle cx="601" cy="217" r="137" fill="var(--green)"/>
  <path d="M574 354 A27 27 0 0 1 628 354 Z" fill="#fff"/>
  <polyline points="595,337 601,342 607,337" fill="none" stroke="var(--green)" stroke-width="2.5"/>
  <polyline points="595,343 601,348 607,343" fill="none" stroke="var(--green)" stroke-width="2.5"/>
  <!-- right -->
  <circle cx="942" cy="217" r="137" fill="#fff" stroke="var(--charcoal)" stroke-width="4"/>
  <path d="M829.4 295 A137 137 0 0 0 1054.6 295 Z" fill="var(--charcoal)"/>
  <!-- icons -->
  <g fill="none" stroke="#555" stroke-width="2.5">
    <ellipse cx="247" cy="124" rx="11" ry="14" transform="rotate(-35 247 124)"/>
    <ellipse cx="265" cy="124" rx="11" ry="14" transform="rotate(35 265 124)"/>
    <line x1="240" y1="147" x2="254" y2="135"/><line x1="272" y1="147" x2="258" y2="135"/>
  </g>
  <g fill="none" stroke="#fff" stroke-width="2.5">
    <rect x="572" y="112" width="58" height="36"/>
    <line x1="601" y1="112" x2="601" y2="148"/>
    <line x1="572" y1="120" x2="630" y2="120"/><line x1="572" y1="140" x2="630" y2="140"/>
    <line x1="584" y1="120" x2="584" y2="140"/><line x1="618" y1="120" x2="618" y2="140"/>
  </g>
  <g fill="var(--charcoal)">
    <circle cx="932" cy="116" r="6"/><circle cx="954" cy="116" r="6"/>
    <rect x="920" y="126" width="46" height="6"/>
    <rect x="926" y="132" width="6" height="18"/><rect x="954" y="132" width="6" height="18"/>
  </g>
</svg>

<div class="abs principle" style="left:141px;top:947px"><h3>PROFICIENCY</h3><p>Nemo enim ipsam voluptatem quia voluptas sit aspernatur aut odit aut fugit.</p></div>
<div class="abs principle is-active" style="left:486px;top:947px"><h3>LESSONS</h3><p>Nemo enim ipsam voluptatem quia voluptas sit aspernatur aut odit aut fugit.</p></div>
<div class="abs principle" style="left:827px;top:947px"><h3>TEAMWORK</h3><p>Nemo enim ipsam voluptatem quia voluptas sit aspernatur aut odit aut fugit.</p></div>
<div class="abs cap-label" style="left:141px;top:1089px">Our Approach</div>
<div class="abs cap-label" style="left:827px;top:1089px">Let's Talk</div>

<!-- Testimonials -->
<section class="abs testimonials" role="img" aria-label="Dim photo of a tennis player on court at dusk"></section>
<div class="abs eyebrow" style="top:1351px;color:#fff">TENNIS CLUB</div>
<h2 class="abs section-title" style="top:1376px;color:#fff">PLAYER TESTIMONIALS</h2>
<div class="abs rule" style="top:1447px;background:#fff"></div>
<svg class="abs" style="left:38px;top:1610px" width="24" height="40"><polyline points="20,2 4,20 20,38" fill="none" stroke="#fff" stroke-width="2.5"/></svg>
<svg class="abs" style="left:1140px;top:1610px" width="24" height="40"><polyline points="4,2 20,20 4,38" fill="none" stroke="#fff" stroke-width="2.5"/></svg>
<div class="abs avatar" role="img" aria-label="Portrait of club member Daniel Marsh"></div>
<div class="abs quote-badge">//</div>
<div class="abs person">DANIEL MARSH</div>
<p class="abs quote">“Sed ut perspiciatis unde omnis iste natus error sit voluptatem accusantium doloremque laudantium, totam rem aperiam, eaque ipsa quae ab illo inventore veritatis et quasi architecto beatae vitae dicta sunt explicabo.”</p>

<!-- Programmes -->
<section class="abs programmes">
  <div class="abs programme" style="left:19px;top:19px">
    <div class="photo" role="img" aria-label="Senior players at the net on a clay court" style="background:linear-gradient(160deg,#d9cbb8,#b0653f)"></div>
    <div class="badge" style="background:var(--charcoal)"><svg width="26" height="26"><circle cx="17" cy="7" r="4" fill="#fff"/><line x1="4" y1="22" x2="15" y2="12" stroke="#fff" stroke-width="3"/></svg></div>
    <h3>SENIOR TEAM</h3><p>Nemo enim ipsam voluptatem quia voluptas sit aspernatur aut odit aut fugit, sed quias</p>
  </div>
  <div class="abs programme" style="left:263px;top:19px">
    <div class="photo" role="img" aria-label="Player in red reaching for a ball on clay" style="background:linear-gradient(160deg,#e9e4dc,#c8744a)"></div>
    <div class="badge" style="background:var(--green)"><svg width="26" height="26" fill="none" stroke="#fff" stroke-width="2"><rect x="3" y="6" width="20" height="14"/><line x1="13" y1="6" x2="13" y2="20"/><line x1="3" y1="13" x2="23" y2="13"/></svg></div>
    <h3>TRAINING COURSE</h3><p>Nemo enim ipsam voluptatem quia voluptas sit aspernatur aut odit aut fugit, sed quias</p>
  </div>
  <div class="abs programme" style="left:510px;top:19px">
    <div class="photo" role="img" aria-label="Coach and child playing on an outdoor clay court" style="background:linear-gradient(160deg,#9fb59a,#c0714a)"></div>
    <div class="badge" style="background:var(--charcoal)"><svg width="26" height="26" fill="none" stroke="#fff" stroke-width="2.5"><circle cx="13" cy="10" r="6"/><line x1="5" y1="23" x2="21" y2="23"/></svg></div>
    <h3>PARTICIPATION</h3><p>Nemo enim ipsam voluptatem quia voluptas sit aspernatur aut odit aut fugit, sed quias</p>
  </div>
  <div class="abs programme" style="left:757px;top:19px">
    <div class="photo" role="img" aria-label="Tennis ball flying over a floodlit blue court" style="background:linear-gradient(170deg,#0e1f3a,#1f5f9c 70%,#2a86c4)"></div>
    <div class="badge" style="background:var(--green)"><svg width="26" height="26" fill="none" stroke="#fff" stroke-width="2.5"><circle cx="15" cy="10" r="7"/><line x1="10" y1="15" x2="3" y2="23"/></svg></div>
    <h3 style="color:var(--green)">BASIC TACTICS</h3><p>Nemo enim ipsam voluptatem quia voluptas sit aspernatur aut odit aut fugit, sed quias</p>
  </div>
</section>

<!-- Gallery -->
<div class="abs eyebrow" style="top:2307px">TENNIS CLUB</div>
<h2 class="abs section-title" style="top:2330px">OUR <em>GALLERY</em></h2>
<div class="abs rule" style="top:2403px"></div>
<section class="abs gallery">
  <div class="abs tile" style="left:19px;top:19px;width:294px;height:205px;background:linear-gradient(170deg,#8a8f85 0%,#3f86c4 45%,#1d5fa5 100%)" role="img" aria-label="Swimming pool beside the clubhouse">SWIMMING POOL</div>
  <div class="abs tile" style="left:19px;top:245px;width:294px;height:290px;background:linear-gradient(170deg,#5e6a63,#3b4440)" role="img" aria-label="Rendering of the hard tennis courts">
    <svg class="abs" style="left:124px;top:128px" width="46" height="30" viewBox="0 0 46 30"><path d="M2 15 Q23 -6 44 15 Q23 36 2 15Z" fill="none" stroke="#fff" stroke-width="3"/><circle cx="23" cy="15" r="6" fill="#fff"/></svg>HARD TENNIS COURTS</div>
  <div class="abs tile" style="left:332px;top:19px;width:340px;height:516px;background:linear-gradient(180deg,#5f86b5 0%,#a9b8c6 40%,#6d8a74 70%,#6f6e69 100%)" role="img" aria-label="Clay tennis courts under a cloudy sky with a rainbow">CLAY TENNIS COURTS</div>
  <div class="abs tile" style="left:691px;top:19px;width:294px;height:205px;background:linear-gradient(170deg,#d8d8d8,#9a9a9a)" role="img" aria-label="Clubhouse architectural rendering, side view">CLUBHOUSE</div>
  <div class="abs tile" style="left:691px;top:245px;width:294px;height:290px;background:linear-gradient(170deg,#8c8c8c,#4f4f4f)" role="img" aria-label="Clubhouse architectural rendering, front view">CLUBHOUSE</div>
</section>

<!-- Footer -->
<footer class="abs footer"></footer>
<svg class="abs" style="left:834px;top:3097px" width="366" height="332" viewBox="0 0 366 332"><polygon points="0,0 366,0 366,332" fill="#fff"/></svg>
<div class="abs footer-brand"><span class="dot"></span>Willow Fen</div>
<div class="abs contact" style="left:98px">
  <span class="ring"><svg width="18" height="18" viewBox="0 0 24 24"><path d="M6.6 10.8a15 15 0 0 0 6.6 6.6l2.2-2.2c.3-.3.7-.4 1-.2 1.1.4 2.3.6 3.6.6.6 0 1 .4 1 1V20c0 .6-.4 1-1 1A17 17 0 0 1 3 4c0-.6.4-1 1-1h3.5c.6 0 1 .4 1 1 0 1.3.2 2.5.6 3.6.1.3 0 .7-.2 1z" fill="#fff"/></svg></span>180 555 0142
</div>
<div class="abs contact" style="left:304px">
  <span class="ring"><svg width="18" height="14" viewBox="0 0 18 14"><rect x="1" y="1" width="16" height="12" fill="none" stroke="#fff" stroke-width="2"/><polyline points="1,1 9,8 17,1" fill="none" stroke="#fff" stroke-width="2"/></svg></span>info@willowfen.com
</div>
<nav class="abs footer-nav"><span>HOME</span><span class="sep">|</span><span>ABOUT</span><span class="sep">|</span><span>MEMBERSHIP</span><span class="sep">|</span><span>SCHEDULE</span><span class="sep">|</span><span>CONTACT</span></nav>
<div class="abs footer-line"></div>
<div class="abs copyright">Copyright © 2018 Willow Fen. All Rights Reserved.</div>

</body>
</html>
```